Info Graphic about Maple Orchard Restaurant

This info graphic should detail all releavent details about Maple Orchard, such as opening hours, accepted payment methods, home delivery areas etc. please refer attached word document for details.

Also attached a pdf with old info graphic.

IMPORTANT:. Given there is lot of text, I expect the designer to make this interesting. This will be printed in A1 and also A4
Also, I need this in both Portrait and landscape designs.

Industry/Entity Type

Hospitality

Font styles to use
Serif
Sans Serif
Decorative
Script
Other font styles liked:
• I let designer choose

Colors

Designer to choose colors to be used in the design.

Requirements
Must have
• Refer attached word doc
Nice to have
• Refer attached word doc
Should not have
• Refer attached word doc

```html
<!DOCTYPE html>
<html lang="en">
<head>
<meta charset="utf-8">
<title>Maple Orchard Indian Restaurant – Info</title>
<link href="https://fonts.googleapis.com/css2?family=Berkshire+Swash&family=Oswald:wght@400;500;600&family=Roboto:wght@400;500;700&display=swap" rel="stylesheet">
<style>
  :root{
    --orange:#f28a1e;
    --heading:#f5891f;
    --title-red:#b3252c;
    --panel:#161616;
    --text:#ffffff;
    --tick:#b9c23a;
    --cross:#e3262b;
    --strip:#f3efe9;
  }
  *{margin:0;padding:0;box-sizing:border-box}
  html,body{width:849px;height:1200px;overflow:hidden;background:#fff}
  .poster{position:relative;width:849px;height:1200px;overflow:hidden;font-family:'Roboto',sans-serif;color:var(--text)}
  .food-backdrop{position:absolute;inset:0;background:
    radial-gradient(ellipse at 30% 45%,#d98a3a 0%,#b7652a 35%,#8a4422 65%,#5b3a22 100%)}
  .header{position:absolute;left:0;top:0;width:849px;height:172px}
  .chilli{position:absolute;top:20px;width:64px;height:104px;border-radius:30px;background:linear-gradient(90deg,#c6281e,#e9641c,#c9b532)}
  .chilli.left{left:30px}.chilli.right{right:30px}
  .title{position:absolute;top:26px;left:0;width:849px;text-align:center;font-family:'Berkshire Swash',serif;font-size:43px;color:var(--title-red);white-space:nowrap}
  .site{position:absolute;top:76px;left:0;width:849px;text-align:center;font-size:23px;letter-spacing:4.6px;color:#1a1a1a}
  .panel{position:absolute;left:58px;top:210px;width:733px;height:866px;background:var(--panel);border-radius:20px}
  .h{position:absolute;font-family:'Oswald',sans-serif;font-weight:500;color:var(--heading);text-align:center;white-space:nowrap;line-height:1}
  .note{position:absolute;font-family:'Oswald',sans-serif;font-size:15px;font-variant:small-caps;color:#eee;line-height:24px}
  table{border-collapse:collapse}
  .hours{position:absolute;left:81px;top:296px;width:325px;height:142px}
  .hours td,.hours th{border:1.5px solid #fff;font-size:17px;text-align:left;padding:0 10px;line-height:20px}
  .hours th{font-weight:500;height:30px}
  .hours .first{border-right:none}
  .suburbs{position:absolute;top:594px;font-size:17px;line-height:28.4px}
  .body-text{position:absolute;left:81px;font-size:16.5px;line-height:25px}
  .contact{position:absolute;left:450px;display:flex;align-items:center;gap:10px;font-size:18px}
  .icon{width:32px;height:32px;border-radius:50%;background:var(--orange);display:flex;align-items:center;justify-content:center}
  .pay{position:absolute;left:442px;top:518px;width:326px}
  .pay td{border:1.5px solid #fff;height:31.4px;font-size:18px;font-weight:700;padding:0 6px}
  .pay .mark{border-left:none;text-align:right;width:50px}
  .pay .name{border-right:none}
  .services{position:absolute;left:455px;top:832px;list-style:none;font-size:23px;line-height:27.4px}
  .services li::before{content:"•";display:inline-block;width:34px;font-size:22px}
  .strip{position:absolute;left:0;top:1132px;width:849px;height:68px;background:var(--strip);opacity:.92}
  .badge{position:absolute;top:1146px}
</style>
</head>
<body>
<div class="poster">
  <div class="food-backdrop" role="img" aria-label="Close-up photo of a bowl of Indian curry"></div>

  <div class="header">
    <svg width="849" height="172" viewBox="0 0 849 172"><polygon points="0,0 849,0 849,128 430,170 0,128" fill="var(--orange)"/></svg>
    <div class="chilli left" role="img" aria-label="Illustration of red and yellow chillies"></div>
    <div class="chilli right" role="img" aria-label="Illustration of red and yellow chillies"></div>
    <div class="title">Maple Orchard Indian Restaurant</div>
    <div class="site">www.mapleorchard.com.au</div>
  </div>

  <div class="panel"></div>

  <div class="h" style="left:81px;width:325px;top:246px;font-size:29px">OPENING HOURS</div>
  <table class="hours">
    <tr><th style="width:115px"></th><th style="width:108px">Morning</th><th>Evening</th></tr>
    <tr><td>Monday to<br>Friday</td><td>11:30AM-<br>2:30PM</td><td>5:00PM-<br>9:00PM</td></tr>
    <tr><td>Saturday to<br>Sunday</td><td>10:30AM-<br>2:30PM</td><td>5:00PM-<br>9:00PM</td></tr>
  </table>
  <div class="note" style="left:89px;top:442px">Dinner Buffet is available only from Mon-Thu from<br>5:30PM-8:30PM</div>

  <div class="h" style="left:81px;width:325px;top:508px;font-size:29px;line-height:43px">WE DELIVER TO THE<br>FOLLWING SUBURBS</div>
  <div class="suburbs" style="left:104px">Beldon<br>Craigie<br>Darch<br>Duncraig<br>Edgewater<br>Greenwood<br>Woodvale</div>
  <div class="suburbs" style="left:325px">Hocking<br>Kingsley<br>Madeley<br>Padbury<br>Pearsall<br>Wangara</div>

  <div class="h" style="left:81px;width:325px;top:801px;font-size:27px">DISCOUNT VOUCHERS</div>
  <div class="body-text" style="top:836px">We accept leisure book vouchers<br>and maple orchard supplied discount vouchers.</div>
  <div class="body-text" style="top:903px">Leisure vouchers are eligible only<br>for dine-in</div>

  <div class="h" style="left:58px;width:370px;top:983px;font-size:30px">BYO (BRING YOUR OWN)</div>
  <div class="body-text" style="left:58px;width:370px;text-align:center;top:1020px;font-size:19px">Wine only - Corkage per bottle apply</div>

  <div class="h" style="left:440px;width:334px;top:245px;font-size:30px">BOOKING/ORDERS CONTACT</div>
  <div class="contact" style="top:302px"><span class="icon"><svg width="16" height="16" viewBox="0 0 24 24"><path d="M6.6 10.8a15 15 0 0 0 6.6 6.6l2.2-2.2a1 1 0 0 1 1-.25 11 11 0 0 0 3.6.6 1 1 0 0 1 1 1V20a1 1 0 0 1-1 1A17 17 0 0 1 3 4a1 1 0 0 1 1-1h3.5a1 1 0 0 1 1 1c0 1.25.2 2.45.6 3.6a1 1 0 0 1-.25 1z" fill="#161616"/></svg></span>08 9000 0000</div>
  <div class="contact" style="top:348px"><span class="icon"><svg width="18" height="14" viewBox="0 0 18 14"><rect x="1" y="1" width="16" height="12" fill="none" stroke="#161616" stroke-width="1.6"/><polyline points="1,1 9,8 17,1" fill="none" stroke="#161616" stroke-width="1.6"/></svg></span>admin@mapleorchard.com.au</div>
  <div class="contact" style="top:394px"><span class="icon"><svg width="18" height="18" viewBox="0 0 20 20" fill="none" stroke="#161616" stroke-width="1.5"><circle cx="10" cy="10" r="8"/><ellipse cx="10" cy="10" rx="3.5" ry="8"/><line x1="2" y1="10" x2="18" y2="10"/><line x1="3.5" y1="6" x2="16.5" y2="6"/><line x1="3.5" y1="14" x2="16.5" y2="14"/></svg></span>www.mapleorchard.com.au</div>

  <div class="h" style="left:440px;width:334px;top:472px;font-size:30px">PAYMENT METHODS</div>
  <table class="pay">
    <tr><td class="name">Cash</td><td class="mark"><svg width="30" height="24"><polyline points="3,13 11,21 27,3" fill="none" stroke="var(--tick)" stroke-width="5"/></svg></td></tr>
    <tr><td class="name">Paylink</td><td class="mark"><svg width="30" height="24"><polyline points="3,13 11,21 27,3" fill="none" stroke="var(--tick)" stroke-width="5"/></svg></td></tr>
    <tr><td class="name">Nova/Crest</td><td class="mark"><svg width="30" height="24"><polyline points="3,13 11,21 27,3" fill="none" stroke="var(--tick)" stroke-width="5"/></svg></td></tr>
    <tr><td class="name">Debit/Credit</td><td class="mark"><svg width="30" height="24"><polyline points="3,13 11,21 27,3" fill="none" stroke="var(--tick)" stroke-width="5"/></svg></td></tr>
    <tr><td class="name">Orbix*</td><td class="mark"><svg width="30" height="24"><polyline points="3,13 11,21 27,3" fill="none" stroke="var(--tick)" stroke-width="5"/></svg></td></tr>
    <tr><td class="name">Kinta*</td><td class="mark"><svg width="30" height="24"><polyline points="3,13 11,21 27,3" fill="none" stroke="var(--tick)" stroke-width="5"/></svg></td></tr>
    <tr><td class="name">Dinerva</td><td class="mark"><svg width="30" height="24"><path d="M8 3 L22 21 M22 3 L8 21" stroke="var(--cross)" stroke-width="4"/></svg></td></tr>
  </table>
  <div class="note" style="left:449px;top:744px">* Surcharge of 2.8% apply</div>

  <div class="h" style="left:440px;width:298px;top:797px;font-size:30px">SERVICES</div>
  <ul class="services">
    <li>Functions/Parties</li><li>Bulk cooking</li><li>Special orders</li><li>Business meetings</li><li>Seminars/Presentations</li>
  </ul>
  <div class="h" style="left:440px;width:334px;top:985px;font-size:27px">OUTSIDE FOOD IS NOT ALLOWED!</div>

  <div class="strip"></div>
  <svg class="badge" style="left:172px" width="100" height="40" role="img" aria-label="Partner badge"><rect x="0" y="6" width="100" height="28" rx="6" fill="#2e3c8c"/></svg>
  <svg class="badge" style="left:344px" width="100" height="40" role="img" aria-label="Partner badge"><rect x="0" y="8" width="100" height="24" rx="6" fill="#2d5fa6"/></svg>
  <svg class="badge" style="left:516px" width="44" height="44" role="img" aria-label="Partner badge"><circle cx="22" cy="20" r="20" fill="#6d6a63"/></svg>
  <svg class="badge" style="left:634px" width="44" height="44" role="img" aria-label="Partner badge"><circle cx="22" cy="20" r="20" fill="#3e9a4a"/></svg>
</div>
</body>
</html>
```